Roadside building business signage for a holistic health clinic.

Replace signs as shown in the attached file. They are perforated stickers that go on the windows as shown. Looking for something that has our logo and says the name of the practice with logo (Fernridge Health & Wellness) also boldly says Acupuncture, IV Vitamins, and Holistic Health.
Possibly our phone number as well 318-562-7041
Updates

Please don't use pink except the logo. Earthy, organic tone colors appreciated.

Need of eye catching window signage of a holistic clinic on a brick building. Pink, purple, sage green, white color. Logo is pink on a white background. Please don't overload with too much pink. Words to include are "Fernridge Health and Wellness(name of business)", "Direct Primary Care", " Medical acupuncture", "IV Vitamin Therapy", "fernridgecareclinic.example","318-562-7041".

Target Market(s)

People will see in their cars passing by the building. Busy roadside so need to be visible while passing in fast speed.

Industry/Entity Type

Health & Wellness

Font styles to use
Sans Serif

Colors

Designer to choose colors to be used in the design.

Requirements
Must have
• On sign must have words Holistic Medicine, Medical Acupuncture, Direct Primary Care and IV vitamins.
Nice to have
• Simple, minimalistic, artistic yet has clear message. White, Black, Violet, Pink (logo), Dark green, Sage green.
Should not have
• Bold colors (red, yellow, blue), same tone colors. Blue waves on the current signage (uploaded file) must go.

```html
<!DOCTYPE html>
<html lang="en">
<head>
<meta charset="utf-8">
<title>Fernridge Health &amp; Wellness – Window Signage</title>
<link rel="stylesheet" href="https://fonts.googleapis.com/css2?family=Marcellus&family=PT+Sans+Narrow&display=swap">
<style>
  :root {
    --backdrop: #e9e6e0;
    --cream: #f4f0e6;
    --sage: #5f8a72;
    --sage-soft: #b3c8ba;
    --sage-tint: #7a9e89;
    --forest: #1f4d3f;
    --ink-light: #f4f0e6;
    --bloom: #d94f8f;
  }
  * { box-sizing: border-box; margin: 0; padding: 0; }
  html, body { width: 900px; height: 1200px; overflow: hidden; }
  body { background: var(--backdrop); position: relative; font-family: "PT Sans Narrow", sans-serif; }

  .panel { position: absolute; overflow: hidden; }
  .panel--cream { background: var(--cream); }
  .panel--sage { background: var(--sage); }

  .arch { position: absolute; left: 210px; top: 110px; width: 480px; height: 304px; }

  .headline {
    position: absolute; top: 205px;
    font-family: "Marcellus", sans-serif;
    font-size: 38px; line-height: 1.06; letter-spacing: 1px;
    color: var(--forest); text-transform: uppercase;
  }
  .headline--left { right: 475px; text-align: right; }
  .headline--right { left: 475px; text-align: left; }

  .tint-band {
    position: absolute; left: 0; bottom: 0; width: 100%; height: 110px;
    background: linear-gradient(to bottom, var(--cream), var(--sage-soft));
  }

  .brand { position: absolute; left: 0; right: 0; top: 36px; text-align: center; color: var(--forest); font-family: "Marcellus", sans-serif; }
  .brand__mark { width: 58px; height: 58px; border-radius: 50%; background: var(--bloom); margin: 0 auto 16px; }
  .brand__name { font-size: 34px; letter-spacing: 3px; line-height: 1; }
  .brand__tagline { font-size: 11px; letter-spacing: 3px; margin-top: 6px; }

  .services { position: absolute; top: 44px; list-style: none; color: var(--ink-light); font-size: 22px; line-height: 38px; }
  .services--left { right: 20px; text-align: right; }
  .services--right { left: 20px; text-align: left; }

  .contact { position: absolute; top: 80px; left: 0; right: 0; text-align: center; color: var(--ink-light); }
  .contact__phone { display: inline-block; border: 1px solid var(--ink-light); border-radius: 6px; padding: 3px 9px; font-size: 18px; }
  .contact__web { font-size: 10px; margin-top: 10px; color: var(--ink-light); }

  .accent-area {
    position: absolute; bottom: 0; width: 60px; height: 70px;
    background: linear-gradient(to top, var(--sage-tint), var(--sage));
  }
  .accent-area--left { left: 0; }
  .accent-area--right { right: 0; }
</style>
</head>
<body>

  <svg class="arch" viewBox="0 0 480 304" aria-hidden="true">
    <path d="M0 304 V170 C0 80 110 20 240 0 C370 20 480 80 480 170 V304 Z" fill="var(--cream)"/>
    <rect x="230" y="0" width="20" height="304" fill="var(--backdrop)"/>
  </svg>
  <h2 class="headline headline--left">Direct<br>Holistic<br>Primary<br>Care</h2>
  <h2 class="headline headline--right">Direct<br>Holistic<br>Primary<br>Care</h2>

  <div class="panel panel--cream" style="left:70px;top:470px;width:134px;height:270px;">
    <div class="tint-band" role="img" aria-label="Decorative sage landscape band"></div>
  </div>
  <div class="panel panel--cream" style="left:210px;top:420px;width:230px;height:320px;">
    <div class="brand">
      <div class="brand__mark"></div>
      <div class="brand__name">FERNRIDGE</div>
      <div class="brand__tagline">HEALTH &amp; WELLNESS</div>
    </div>
    <div class="tint-band" role="img" aria-label="Decorative sage landscape band"></div>
  </div>

  <div class="panel panel--cream" style="left:460px;top:420px;width:230px;height:320px;">
    <div class="brand">
      <div class="brand__mark"></div>
      <div class="brand__name">FERNRIDGE</div>
      <div class="brand__tagline">HEALTH &amp; WELLNESS</div>
    </div>
    <div class="tint-band" role="img" aria-label="Decorative sage landscape band"></div>
  </div>
  <div class="panel panel--cream" style="left:696px;top:470px;width:134px;height:270px;">
    <div class="tint-band" role="img" aria-label="Decorative sage landscape band"></div>
  </div>

  <div class="panel panel--sage" style="left:20px;top:746px;width:44px;height:334px;"></div>
  <div class="panel panel--sage" style="left:70px;top:746px;width:134px;height:334px;">
    <div class="contact">
      <div class="contact__phone">318-562-7041</div>
      <div class="contact__web">fernridgecareclinic.example</div>
    </div>
    <div class="accent-area accent-area--left" role="img" aria-label="Decorative line-art flower ornament"></div>
  </div>
  <div class="panel panel--sage" style="left:210px;top:746px;width:230px;height:334px;">
    <ul class="services services--left">
      <li>Holistic Medicine</li>
      <li>Medical Acupuncture</li>
      <li>Direct Primary Care</li>
      <li>IV vitamins</li>
    </ul>
  </div>

  <div class="panel panel--sage" style="left:460px;top:746px;width:230px;height:334px;">
    <ul class="services services--right">
      <li>Holistic Medicine</li>
      <li>Medical Acupuncture</li>
      <li>Direct Primary Care</li>
      <li>IV vitamins</li>
    </ul>
  </div>
  <div class="panel panel--sage" style="left:696px;top:746px;width:134px;height:334px;">
    <div class="contact">
      <div class="contact__phone">318-562-7041</div>
      <div class="contact__web">fernridgecareclinic.example</div>
    </div>
    <div class="accent-area accent-area--right" role="img" aria-label="Decorative line-art flower ornament"></div>
  </div>
  <div class="panel panel--sage" style="left:836px;top:746px;width:44px;height:334px;"></div>

</body>
</html>
```